Casino with the 'highest winning percentage' needs a stationery design

This is for a casino in Colombo, Sri Lanka and we need a stationery design for business card, letter head and envelope.

Should be very professional, simple and elegant without fancy fonts

Reason: Not fully satisfied with the designs. Need more designs.

Business

• 1. card deck symbol 'CLUBS' in red, or black

2. name in BLOCK CAPITAL LETTERS

3. Preferred font colours are black, white or red

4. Prefer 'professional /elegant' fonts
• SHOULD NOT HAVE ANY OTHER SYMBOL EXCEPT 'CLUBS'

DO NOT PREFER ITALIC FONTS

```html
<!DOCTYPE html>
<html lang="en">
<head>
<meta charset="utf-8">
<title>Marlow's Entertainment — Stationery</title>
<link rel="stylesheet" href="https://fonts.googleapis.com/css2?family=Noto+Serif:wght@400;700&family=Jost:wght@400;500&display=swap">
<style>
:root{
  --red:#d4303a;
  --ink:#1a1a1a;
  --paper:#ffffff;
  --paper-shade:#ececec;
  --grey:#555;
  --stage:#e6e2dc;
  --serif:"Noto Serif", Georgia, serif;
  --sans:"Jost", Arial, sans-serif;
}
*{margin:0;padding:0;box-sizing:border-box}
html,body{width:1200px;height:486px;overflow:hidden;background:var(--stage)}
.canvas{position:relative;width:1200px;height:486px}
.sheet,.envelope,.card{position:absolute;background:linear-gradient(160deg,var(--paper) 40%,var(--paper-shade));box-shadow:0 2px 6px rgba(0,0,0,.25)}
.brand{position:absolute;display:flex;align-items:center;gap:7px}
.brand-dot{width:24px;height:24px;border-radius:50%;background:var(--red);flex:none}
.brand-name{font-family:var(--serif);font-weight:700;font-size:13px;line-height:1.15;color:var(--ink);letter-spacing:.3px}
.contact-list{position:absolute;list-style:none;font-family:var(--serif);font-size:6px;color:var(--grey);line-height:8.2px}
.contact-list span{color:var(--red);margin-right:3px}
.footer-rule{position:absolute;left:0;right:0;height:1.5px;background:var(--ink)}
.footer-band{position:absolute;left:0;right:0;background:var(--red);color:#fff;font-family:var(--serif);text-align:center}

/* letterhead */
.letterhead{left:8px;top:30px;width:340px;height:440px}
.letterhead .brand{left:14px;top:14px}
.letterhead .contact-list{left:258px;top:12px;padding-left:6px;border-left:1px solid #ccc}
.letterhead .watermark{position:absolute;left:108px;top:160px;width:104px;height:104px;border-radius:50%;background:rgba(212,48,58,.08)}
.letterhead .footer-rule{top:414px}
.letterhead .footer-band{top:418px;height:22px;font-size:7.5px;line-height:22px;text-align:left;padding-left:30px}
.letterhead .footer-band b{font-weight:700}

/* fax */
.fax{left:363px;top:30px;width:340px;height:440px}
.fax .brand{left:98px;top:14px}
.fax-title{position:absolute;left:13px;top:100px;font-family:var(--sans);font-size:22px;color:var(--ink);letter-spacing:.5px}
.fax-row{position:absolute;left:13px;width:290px;height:14px;border-bottom:1px solid #333;font-family:var(--sans);font-size:6px;color:var(--ink)}
.fax-row .right{position:absolute;left:173px}
.fax-options{position:absolute;left:13px;top:225px;display:flex;gap:20px;font-family:var(--sans);font-size:6px;color:var(--ink)}
.fax-options span{display:flex;align-items:center;gap:4px}
.fax-options i{width:7px;height:7px;border:1px solid #333;display:inline-block}
.fax .footer-rule{top:414px}
.fax .footer-band{top:418px;height:22px;font-size:5.5px;line-height:8px;padding-top:3px}

/* envelopes */
.envelope-back{left:812px;top:0;width:372px;height:184px;background:var(--paper)}
.envelope-flap{left:730px;top:86px;width:380px;height:170px}
.envelope-front{left:770px;top:162px;width:380px;height:170px}
.envelope-front .brand{left:11px;top:12px}
.envelope-front .address{position:absolute;left:54px;top:48px;font-family:var(--serif);font-size:6.5px;line-height:8px;color:var(--ink)}
.envelope-front .footer-rule{top:157px;height:1px}
.envelope-front .footer-band{top:159px;height:11px;font-size:6px;line-height:11px;letter-spacing:1.5px}

/* business card */
.card-front{left:759px;top:354px;width:207px;height:118px}
.card-front .brand{left:38px;top:14px}
.tagline{position:absolute;left:0;right:0;top:59px;text-align:center;font-family:var(--serif);font-weight:700;font-size:5px;color:var(--red);letter-spacing:.4px}
.card-front .footer-rule{top:68px;height:1px}
.card-band{position:absolute;left:0;right:0;top:70px;height:48px;background:var(--red);color:#fff;font-family:var(--serif)}
.card-band .company{position:absolute;right:110px;top:9px;text-align:right;font-size:5px;line-height:6.4px}
.card-band .company b{display:block;font-size:6.5px;margin-bottom:3px}
.card-band .contact-list{left:103px;top:5px;padding-left:6px;border-left:1px solid rgba(255,255,255,.6);color:#fff;font-size:5px;line-height:7.6px}
.card-band .contact-list span{color:#fff}
.card-back{left:977px;top:354px;width:207px;height:118px;background:var(--paper)}
.suit-art{position:absolute;left:50px;top:8px;width:110px;height:104px;background:linear-gradient(90deg,rgba(60,60,60,.12),rgba(212,48,58,.12))}
.card-back-name{position:absolute;left:0;right:0;top:38px;text-align:center;font-family:var(--serif);font-weight:700;font-size:15px;line-height:17px;color:var(--ink)}
.card-back-name small{display:block;font-size:11px;line-height:15px}
</style>
</head>
<body>
<main class="canvas">

  <section class="sheet letterhead">
    <div class="brand"><span class="brand-dot"></span><span class="brand-name">MARLOW'S<br>ENTERTAINMENT</span></div>
    <ul class="contact-list">
      <li><span>&#9742;</span>+ 94 11 2480375</li>
      <li><span>&#9632;</span>+ 94 11 0000000</li>
      <li><span>&#9993;</span>info@marlowscolombo.com</li>
      <li><span>&#9679;</span>www.marlowscolombo.com</li>
    </ul>
    <div class="watermark"></div>
    <div class="footer-rule"></div>
    <div class="footer-band"><b>MARLOW'S LIMITED</b> / 58, Harbour View Road, Colombo 01000, Sri Lanka</div>
  </section>

  <section class="sheet fax">
    <div class="brand"><span class="brand-dot"></span><span class="brand-name">MARLOW'S<br>ENTERTAINMENT</span></div>
    <h1 class="fax-title">FAX</h1>
    <div class="fax-row" style="top:140px">To :<span class="right">From :</span></div>
    <div class="fax-row" style="top:158px">Fax :<span class="right">Pages :</span></div>
    <div class="fax-row" style="top:176px">Phone :<span class="right">Date :</span></div>
    <div class="fax-row" style="top:194px">Re :<span class="right">CC :</span></div>
    <div class="fax-options">
      <span><i></i>Urgent</span>
      <span><i></i>For Review</span>
      <span><i></i>Please Comment</span>
      <span><i></i>Please Reply</span>
      <span><i></i>Please Recycle</span>
    </div>
    <div class="footer-rule"></div>
    <div class="footer-band">MARLOW'S LIMITED / 58, Harbour View Road, Colombo 01000, Sri Lanka<br>&#9742; + 94 11 2480375 &nbsp;&#9632; + 94 11 0000000 &nbsp;&#9993; info@marlowscolombo.com &nbsp;&#9679; www.marlowscolombo.com</div>
  </section>

  <svg class="envelope envelope-back" viewBox="0 0 372 184" aria-hidden="true">
    <rect width="372" height="184" fill="#fff"/>
    <path d="M0 0H372V14L250 70Q186 90 122 70L0 14Z" fill="var(--red)"/>
  </svg>

  <svg class="envelope envelope-flap" viewBox="0 0 380 170" aria-hidden="true">
    <rect width="380" height="170" fill="#fff"/>
    <path d="M0 0H380V10L260 60Q190 80 120 60L0 10Z" fill="#fff" stroke="#333" stroke-width="1"/>
  </svg>

  <section class="envelope envelope-front">
    <div class="brand"><span class="brand-dot"></span><span class="brand-name">MARLOW'S<br>ENTERTAINMENT</span></div>
    <p class="address">58, Harbour View Road<br>Colombo 01000, Sri Lanka</p>
    <div class="footer-rule"></div>
    <div class="footer-band">www.marlowscolombo.com</div>
  </section>

  <section class="card card-front">
    <div class="brand"><span class="brand-dot"></span><span class="brand-name" style="font-size:11px">MARLOW'S<br>ENTERTAINMENT</span></div>
    <p class="tagline">Highest Winning Percentage In The World</p>
    <div class="footer-rule"></div>
    <div class="card-band">
      <p class="company"><b>MARLOW'S LIMITED</b>58, Harbour View Road<br>Colombo 01000<br>Sri Lanka</p>
      <ul class="contact-list">
        <li><span>&#9742;</span>+ 94 11 2480375</li>
        <li><span>&#9632;</span>+ 94 77 0000000</li>
        <li><span>&#9632;</span>+ 94 11 0000000</li>
        <li><span>&#9993;</span>info@marlowscolombo.com</li>
        <li><span>&#9679;</span>www.marlowscolombo.com</li>
      </ul>
    </div>
  </section>

  <section class="card card-back">
    <div class="suit-art" role="img" aria-label="Faint playing-card suit shapes in grey and red"></div>
    <p class="card-back-name">MARLOW'S<br>ENTERTAINMENT<small>Colombo</small></p>
  </section>

</main>
</body>
</html>
```